NEW Wordpress Website Design for a Dynamic Long Term Healthcare Company in Hawaii

I would like a new website design for my current company, Marlow Health Collective, which has two different brands - Marlow Homecare and Marlow Senior Living. You can see the current website at www.marlowhealth-example.com. The website should be built using Wordpress Software and the Framewise theme. The website should have a local Hawaii island/tropical feel, but look professional for healthcare. I'm looking for something fresh, and want the designer to select colors, styles, etc.

In the Header, on all pages, I would like a menu that includes Home Care, Senior Living, Rates, and About Us.
Under each of the Header Menu Titles, I would like these drop downs included:
Home Care (drop down pages)- Nurse Aide Care, 24-Hour Home Care, Skilled Nursing, Lifestyle Aide, Hospice at Home, Bathing & Meal Service.
Senior Living (drop down pages) - Long-Term Stay, Short-Term Stay.
Rates (drop down page) - Rates.
About Us (drop down pages) - Our Mission, Ohana Talk, About Dana Marlow.

In the footer, on all pages, you should include the address: 248 Pueo Lane, Suite 310, Honolulu, HI 96817. Phone number: 808-555-0172
The footer should also include buttons for a page called Learn, Caregiver Jobs, and each of the service page links to include: Nurse Aide Care, 24-Hour Home Care, Skilled Nursing, Lifestyle Aide, Hospice at Home, Bathing & Meal Service.
Please don't take the current website and redesign a few aspects. I'm looking for a completely different look and feel.

Target Market(s)

40-80 year olds

Industry/Entity Type

Long Term Healthcare

Coding

Coded - Design and coding required

Requirements
Should not have
• Our existing website as a template. We are looking for a complete redesign. Thank you.

```html
<!DOCTYPE html>
<html lang="en">
<head>
<meta charset="utf-8">
<title>Marlow Health Collective — Homecare &amp; Senior Living</title>
<link href="https://fonts.googleapis.com/css2?family=Poppins:ital,wght@0,400;0,500;0,600;0,700;1,600&display=swap" rel="stylesheet">
<style>
:root{
  --teal:#1b5e68;
  --teal-dark:#174f58;
  --coral:#f68778;
  --paper:#f7f7f7;
  --ink:#3e4a4d;
  --muted:#6c7679;
  --white:#ffffff;
  --line:#d9dcdc;
}
*{box-sizing:border-box;margin:0;padding:0}
html,body{width:1200px;height:3425px;overflow:hidden}
body{background:var(--paper);font-family:'Poppins',sans-serif;color:var(--ink);position:relative}
.abs{position:absolute}
a{color:inherit;text-decoration:none}

.site-header{position:absolute;top:0;left:0;width:1200px;height:66px;z-index:5}
.brand{left:245px;top:14px;display:flex;align-items:center;gap:8px;color:var(--teal);font-size:15px;font-weight:600;line-height:1.1}
.brand-dot{width:14px;height:14px;border-radius:50%;background:var(--teal)}
.main-nav{left:520px;top:24px;font-size:10px;color:var(--teal)}
.main-nav span{position:absolute;white-space:nowrap}
.main-nav .active{color:var(--coral)}
.nav-cta{left:813px;top:18px;width:143px;height:26px;background:var(--coral);color:var(--white);font-size:8px;font-weight:600;letter-spacing:1.5px;display:flex;align-items:center;justify-content:center}

.hero-photo{left:0;top:0;width:1200px;height:665px;background:linear-gradient(180deg,#e9e8de 0%,#b9b98f 35%,#8c7a4e 60%,#6b5232 100%)}
.hero-title{left:245px;top:216px;width:700px;font-size:50px;font-weight:600;line-height:68px;color:var(--white);letter-spacing:-.3px}

.tile{position:absolute;padding:18px}
.tile-label{font-size:8.5px;font-weight:600;color:var(--white);display:flex;align-items:center;gap:10px}
.tile-label::after{content:"";width:38px;height:1px;background:currentColor}
.tile-arrow{position:absolute;left:18px;width:22px;height:22px;border:1px solid rgba(255,255,255,.9);display:flex;align-items:center;justify-content:center}
.tile-text{color:var(--white);font-weight:600}
.coral{background:var(--coral)}
.teal{background:var(--teal)}
.photo-dark{background:linear-gradient(135deg,#4a3424,#6d5238 55%,#3b2a1e)}

.eyebrow{font-size:8.5px;font-weight:600;color:var(--teal);display:flex;align-items:center;gap:10px}
.eyebrow::after{content:"";width:38px;height:1px;background:var(--coral)}
.h2{color:var(--teal);font-weight:500}
.btn{background:var(--coral);color:var(--white);font-size:7.5px;font-weight:600;letter-spacing:1.5px;display:flex;align-items:center;justify-content:center}

.service{position:absolute;top:1172px;width:150px}
.service h3{margin-top:18px;font-size:14px;font-weight:500;color:var(--teal);line-height:16px}
.service p{margin-top:12px;font-size:8.5px;line-height:15px;color:var(--muted)}

.stay-rule{left:263px;width:675px;height:1px;background:#333}
.stay-copy{left:600px;width:150px;font-size:8.5px;line-height:15px;color:var(--muted)}
.stay-list{left:769px;list-style:none;font-size:8.5px;line-height:17px;color:var(--teal)}
.stay-list li{display:flex;align-items:center;gap:12px}
.stay-list li::before{content:"";width:8px;height:2px;background:#333}

.stat{position:absolute;top:2481px;width:178px;height:177px;border:1px solid #e4e6e6;background:var(--paper);padding:18px}
.stat b{display:block;margin-top:22px;font-size:54px;font-weight:600;color:var(--teal);line-height:60px}
.stat i{display:block;margin-top:42px;width:18px;height:1px;background:var(--coral)}
.stat span{display:block;margin-top:12px;font-size:12px;font-weight:500;color:var(--teal)}

.field-label{font-size:9px;font-weight:600;color:var(--teal)}
.field-label em{color:#e0473a;font-style:normal}
.field{border:1px solid #cfd3d4;background:var(--white)}
.field-hint{font-size:7px;color:var(--muted)}

.site-footer{left:0;top:3113px;width:1200px;height:312px;background:var(--teal);color:var(--white)}
.foot-col h4{font-size:12px;font-weight:400}
.foot-col ul{list-style:none;margin-top:14px;font-size:9px;line-height:15px}
.foot-contact{font-size:8.5px;line-height:14px}
.foot-btn{height:22px;padding:0 14px;background:var(--coral);color:var(--white);font-size:7.5px;font-weight:600;letter-spacing:1.5px;display:inline-flex;align-items:center}
</style>
</head>
<body>

<div class="abs hero-photo" role="img" aria-label="Photo of three smiling women talking together on a sofa in a bright living room"></div>

<header class="site-header">
  <div class="abs brand"><span class="brand-dot"></span><span>Marlow<br>Senior Living</span></div>
  <nav class="abs main-nav">
    <span class="active" style="left:0">Home Care ⌄</span>
    <span style="left:84px">Senior Living ⌄</span>
    <span style="left:173px">Rates</span>
    <span style="left:218px">About Us ⌄</span>
  </nav>
  <a class="abs nav-cta" href="#">CALL (808) 555-0172</a>
</header>

<h1 class="abs hero-title">Hawaii's Choice Homecare &amp; Senior Living</h1>

<div class="tile teal" style="left:600px;top:665px;width:600px;height:372px"></div>

<div class="tile photo-dark" style="left:244px;top:457px;width:356px;height:208px" role="img" aria-label="Photo of a caregiver in a warm home interior">
  <div class="tile-label">Welcome!</div>
  <p class="tile-text" style="margin-top:22px;font-size:19px;line-height:28px;width:290px">Marlow Homecare provides a variety of professional in-home health care services throughout the entire island of Oahu.</p>
</div>

<div class="tile coral" style="left:600px;top:457px;width:178px;height:208px">
  <div class="tile-label">Contact</div>
  <p class="tile-text" style="margin-top:24px;font-size:17px;font-weight:500">(808) 555-0172</p>
  <p class="tile-text" style="font-size:7.5px">Call for free!</p>
  <div class="tile-arrow" style="top:133px"><svg width="6" height="8" viewBox="0 0 6 8"><path d="M1 1l3 3-3 3" stroke="#fff" fill="none"/></svg></div>
</div>

<div class="tile coral" style="left:778px;top:457px;width:178px;height:208px;border-left:1px solid rgba(255,255,255,.35)">
  <div class="tile-label">Location</div>
  <p class="tile-text" style="margin-top:24px;font-size:12px;line-height:15px">248 Pueo Lane<br>Suite 310 Honolulu, HI<br>96817</p>
  <div class="tile-arrow" style="top:133px"><svg width="6" height="8" viewBox="0 0 6 8"><path d="M1 1l3 3-3 3" stroke="#fff" fill="none"/></svg></div>
</div>

<div class="tile photo-dark" style="left:244px;top:665px;width:356px;height:194px" role="img" aria-label="Photo of residents relaxing in the adult residential care home">
  <p class="tile-text" style="margin-top:6px;font-size:18.5px;line-height:28px;width:290px">Marlow Senior Living, a beautiful Adult Residential Care Home, is located on the windward side of Oahu in Kailua.</p>
</div>

<div class="tile coral" style="left:600px;top:665px;width:178px;height:194px;border-top:1px solid rgba(255,255,255,.35)">
  <div class="tile-label">Certified Care</div>
  <p class="tile-text" style="margin-top:22px;font-size:12px;line-height:15px">We are certified by the Women Owned Business</p>
  <div class="tile-arrow" style="top:132px"><svg width="6" height="8" viewBox="0 0 6 8"><path d="M1 1l3 3-3 3" stroke="#fff" fill="none"/></svg></div>
</div>

<blockquote class="abs" style="left:800px;top:820px;width:140px;text-align:right;color:var(--white);font-size:11.5px;font-weight:600;font-style:italic;line-height:15px;text-decoration:underline">"To care for those who once cared for us is one of the highest honors."</blockquote>
<p class="abs" style="left:820px;top:890px;width:118px;text-align:right;color:var(--white);font-size:8px;font-weight:600;line-height:10px">Dana Marlow<br>Founder</p>
<div class="abs" style="left:845px;top:910px;width:95px;height:65px;background:linear-gradient(120deg,rgba(255,255,255,.04),rgba(255,255,255,.1))" role="img" aria-label="Founder's handwritten signature"></div>

<div class="abs eyebrow" style="left:263px;top:1000px">Respect &amp; Compassion</div>
<h2 class="abs h2" style="left:263px;top:1012px;font-size:25px;display:flex;align-items:center;gap:8px">Our Services <i style="display:inline-block;width:62px;height:2px;background:var(--coral)"></i></h2>
<a class="abs btn" href="#" style="left:263px;top:1068px;width:101px;height:26px">ALL SERVICES</a>

<div class="service" style="left:263px">
  <svg width="32" height="36" viewBox="0 0 32 36"><circle cx="16" cy="10" r="8" fill="var(--coral)"/><rect x="11" y="5" width="10" height="3" fill="#fff"/><path d="M2 36c0-9 6-14 14-14s14 5 14 14z" fill="var(--coral)"/><path d="M16 26v6M13 29h6" stroke="#fff" stroke-width="2"/></svg>
  <h3>NURSING<br>AIDE CARE</h3>
  <p>Lorem ipsum dolor sit amet, adipiscing elit ut elit tellus, luctus mattis consectetur.</p>
</div>
<div class="service" style="left:431px">
  <svg width="36" height="34" viewBox="0 0 36 34"><path d="M18 2L2 16h5v16h22V16h5z" fill="var(--coral)"/><path d="M18 15v10M13 20h10" stroke="#fff" stroke-width="3"/></svg>
  <h3>24-HOUR<br>HOME CARE</h3>
  <p>Lorem ipsum dolor sit amet, adipiscing elit ut elit tellus, luctus mattis consectetur.</p>
</div>
<div class="service" style="left:600px">
  <svg width="36" height="34" viewBox="0 0 36 34"><rect x="2" y="4" width="14" height="26" rx="7" fill="var(--coral)"/><rect x="5" y="17" width="8" height="10" rx="4" fill="#fff"/><circle cx="26" cy="22" r="9" fill="var(--coral)"/><path d="M20 16l12 12" stroke="#fff" stroke-width="2"/></svg>
  <h3>SKILLED<br>NURSING</h3>
  <p>Lorem ipsum dolor sit amet, adipiscing elit ut elit tellus, luctus mattis consectetur.</p>
</div>
<div class="service" style="left:769px">
  <svg width="36" height="34" viewBox="0 0 36 34"><path d="M18 2C9 2 2 8 2 16c0 4 2 7 4 9l-2 7 8-4c2 1 4 1 6 1 9 0 16-6 16-14S27 2 18 2z" fill="var(--coral)"/><path d="M18 9v14M11 16h14" stroke="#fff" stroke-width="3"/></svg>
  <h3>LIFESTYLE<br>AIDE</h3>
  <p>Lorem ipsum dolor sit amet, adipiscing elit ut elit tellus, luctus mattis consectetur.</p>
</div>

<div class="abs stay-rule" style="top:1397px"></div>
<div class="abs eyebrow" style="left:263px;top:1414px">Senior Living</div>
<h2 class="abs h2" style="left:263px;top:1428px;font-size:25px">Long Term Stay</h2>
<p class="abs stay-copy" style="top:1414px">Lorem ipsum dolor sit amet, consectetur adipiscing elit, sed do eiusmod tempor incididunt ut labore et dolore magna aliqua. Ut enim ad veniam, nostrud mattis luctus.</p>
<ul class="abs stay-list" style="top:1413px"><li>Assisted Living</li><li>Safe Environment</li><li>Skilled Nursing</li></ul>

<div class="abs stay-rule" style="top:1535px"></div>
<div class="abs eyebrow" style="left:263px;top:1552px">Senior Living</div>
<h2 class="abs h2" style="left:263px;top:1566px;font-size:25px">Short Term Stay</h2>
<p class="abs stay-copy" style="top:1552px">Lorem ipsum dolor sit amet, consectetur adipiscing elit, sed do eiusmod tempor incididunt ut labore et dolore magna aliqua. Ut enim ad veniam, nostrud mattis luctus.</p>
<ul class="abs stay-list" style="top:1551px"><li>Assisted Living</li><li>Safe Environment</li><li>Skilled Nursing</li></ul>

<div class="abs" style="left:0;top:1715px;width:1200px;height:596px;background:linear-gradient(180deg,#5b4a2e 0%,#7d6a3c 40%,#6a5632 75%,#4b3a24 100%)" role="img" aria-label="Photo of a caregiver chatting with residents in a sunny living room"></div>

<div class="tile teal" style="left:244px;top:1983px;width:356px;height:328px">
  <div class="tile-label">About</div>
  <h2 class="tile-text" style="margin-top:46px;font-size:25px;font-weight:500;line-height:32px">Our mission is to provide the best services.</h2>
  <p style="margin-top:22px;color:var(--white);font-size:8.5px;line-height:15px">At Marlow Health Collective, our mission is to provide compassionate and professional long-term healthcare services that empower individuals to maintain their highest level of independence, health, and well-being in the comfort of their own homes or ours, either through our licensed home healthcare agency – Marlow Homecare, or in our Adult Residential Care Home – Marlow Senior Living.</p>
  <div class="tile-arrow" style="top:288px"><svg width="6" height="8" viewBox="0 0 6 8"><path d="M1 1l3 3-3 3" stroke="#fff" fill="none"/></svg></div>
</div>

<div class="abs" style="left:600px;top:1983px;width:178px;height:163px;background:linear-gradient(160deg,#9fb56a,#4a7fb0 60%,#3a6e9e)" role="img" aria-label="Photo of nurses in blue scrubs sharing a laugh"></div>
<div class="tile coral" style="left:600px;top:2146px;width:178px;height:165px">
  <div class="tile-label">Great Staff</div>
  <p class="tile-text" style="margin-top:22px;font-size:12px;line-height:15px">Our nurses respond every time with a big warm smile.</p>
  <div class="tile-arrow" style="top:124px"><svg width="6" height="8" viewBox="0 0 6 8"><path d="M1 1l3 3-3 3" stroke="#fff" fill="none"/></svg></div>
</div>
<div class="abs" style="left:778px;top:1983px;width:178px;height:328px;background:linear-gradient(180deg,#4f7a3a,#7da05a 45%,#b8b7a4 100%)" role="img" aria-label="Photo of a caregiver helping a senior walk with a walker outdoors"></div>

<div class="abs" style="left:600px;top:2311px;width:178px;height:170px;background:linear-gradient(160deg,#c9b46a,#a08a5a 50%,#5c7f9c)" role="img" aria-label="Photo of a nurse assisting a senior sitting on a bed"></div>
<div class="tile coral" style="left:778px;top:2311px;width:178px;height:170px">
  <div class="tile-label">Safety</div>
  <p class="tile-text" style="margin-top:22px;font-size:12px;line-height:15px">We can provide for our lorem ipsum dolor sit amet nisi.</p>
  <div class="tile-arrow" style="top:128px"><svg width="6" height="8" viewBox="0 0 6 8"><path d="M1 1l3 3-3 3" stroke="#fff" fill="none"/></svg></div>
</div>

<div class="abs eyebrow" style="left:263px;top:2450px">Let the Numbers Speak</div>
<div class="stat" style="left:244px"><b>15</b><i></i><span>Senior Services</span></div>
<div class="stat" style="left:422px"><b>10+</b><i></i><span>Skilled Nurses</span></div>
<div class="stat" style="left:600px"><b>140+</b><i></i><span>Happy Seniors</span></div>
<div class="stat" style="left:778px"><b>28</b><i></i><span>Years of Experience</span></div>

<div class="abs eyebrow" style="left:263px;top:2768px">Contact Us</div>
<h2 class="abs h2" style="left:263px;top:2806px;font-size:25px;line-height:33px">Get in Touch and<br>Let us Care for your<br>Loved Ones.</h2>

<form class="abs" style="left:618px;top:2758px;width:320px;height:260px">
  <div class="abs field-label" style="left:0;top:0">Name <em>*</em></div>
  <div class="abs field" style="left:0;top:14px;width:153px;height:30px"></div>
  <div class="abs field" style="left:166px;top:14px;width:154px;height:30px"></div>
  <div class="abs field-hint" style="left:0;top:50px">First</div>
  <div class="abs field-hint" style="left:166px;top:50px">Last</div>
  <div class="abs field-label" style="left:0;top:72px">Email <em>*</em></div>
  <div class="abs field" style="left:0;top:86px;width:320px;height:30px"></div>
  <div class="abs field-label" style="left:0;top:130px">Message <em>*</em></div>
  <div class="abs field" style="left:0;top:144px;width:320px;height:74px"></div>
  <div class="abs btn" style="left:0;top:229px;width:73px;height:25px">SUBMIT</div>
</form>

<footer class="abs site-footer">
  <h3 class="abs" style="left:244px;top:70px;font-size:18px;font-weight:600">Join Our Mailing List</h3>
  <p class="abs" style="left:244px;top:98px;font-size:8.5px">It elit tellus, luctus nec ullamcorper mattis, pulvinar dapibus leo.</p>
  <div class="abs foot-contact" style="left:244px;top:124px">
    <p>248 Pueo Lane, Suite 310, Honolulu, HI 96817</p>
    <p>Phone: 808-555-0172</p>
  </div>
  <div class="abs" style="left:244px;top:162px;display:flex;gap:10px">
    <a class="foot-btn" href="#">LEARN</a>
    <a class="foot-btn" href="#">CAREGIVER JOBS</a>
  </div>
  <div class="abs foot-col" style="left:600px;top:66px">
    <h4>Our Services</h4>
    <ul><li>Nurse Aide Care</li><li>24-Hour Home Care</li><li>Skilled Nursing</li><li>Lifestyle Aide</li><li>Hospice at Home</li><li>Bathing &amp; Meal Service</li></ul>
  </div>
  <div class="abs foot-col" style="left:794px;top:66px">
    <h4>Follow Us</h4>
    <ul><li>Lanai Social</li><li>Chirpline</li><li>Reelhouse</li><li>Snapgrove</li></ul>
  </div>
  <div class="abs" style="left:0;top:232px;width:1200px;height:1px;background:rgba(255,255,255,.15)"></div>
  <p class="abs" style="left:244px;top:272px;font-size:8px">Copyright © 2024 - Marlow Health Collective. All Rights Reserved.</p>
</footer>

</body>
</html>
```